Personal training and nutrition business needs business card design

We need a business card that outlays our services and invites potential customers to join our team and take the first step to a healthier and more enjoyable life. We cater for any level of fitness and specialize in weight loss and conditioning, strength training, muscle gain and strength endurance. Whether you are just starting off or need some help getting to the next level of your journey we are here to get the job done.
We specialize in one on one or one on two personal training sessions and each program will be custom made to suit individual fitness goals of our clients

```html
<!DOCTYPE html>
<html lang="en">
<head>
<meta charset="utf-8">
<title>Stride &amp; Tempo – Business Card</title>
<link rel="stylesheet" href="https://fonts.googleapis.com/css2?family=Exo+2:ital,wght@1,800&family=Roboto:wght@400;500;700;900&display=swap">
<style>
  :root {
    --bg: #262626;
    --violet-deep: #5a3a8c;
    --violet: #7b4aa6;
    --orchid: #a259a8;
    --pink: #c46fc4;
    --ink: #2b2b2b;
    --paper: #efefef;
    --black: #050505;
    --white: #f4f4f6;
  }
  * { box-sizing: border-box; margin: 0; padding: 0; }
  html, body { width: 1200px; height: 1138px; overflow: hidden; }
  body {
    background: var(--bg);
    font-family: "Roboto", sans-serif;
    position: relative;
  }
  .card {
    position: absolute;
    border-radius: 16px;
    overflow: hidden;
    box-shadow: 0 6px 14px rgba(0,0,0,.45);
  }
  /* Front */
  .card--front {
    left: 274px; top: 186px; width: 623px; height: 376px;
    background: linear-gradient(135deg, var(--violet-deep) 0%, var(--violet) 45%, var(--orchid) 100%);
  }
  .front__brand {
    position: absolute; left: 0; right: 0; top: 146px;
    text-align: center;
    font-weight: 900; font-size: 46px; letter-spacing: 1px;
    color: var(--white); text-transform: uppercase;
  }
  .front__services {
    position: absolute; left: 0; right: 0; top: 207px;
    text-align: center;
    font-weight: 500; font-size: 16px; letter-spacing: 2px;
    color: #e6ddef;
  }
  /* Back */
  .card--back {
    left: 276px; top: 608px; width: 618px; height: 374px;
    background: var(--paper);
  }
  .back__panel { position: absolute; inset: 0; }
  .person__name {
    position: absolute; left: 42px; top: 86px;
    font-family: "Exo 2", sans-serif; font-style: italic; font-weight: 800;
    font-size: 22px; letter-spacing: 1px; color: var(--violet);
  }
  .person__role {
    position: absolute; left: 39px; top: 117px;
    font-size: 16px; color: var(--ink);
  }
  .contact { position: absolute; left: 39px; top: 164px; list-style: none; }
  .contact li {
    display: flex; align-items: center; gap: 14px;
    height: 24px; font-size: 16px; color: var(--ink);
  }
  .contact svg { width: 16px; height: 16px; fill: var(--violet); }
  .address {
    position: absolute; left: 39px; top: 243px;
    font-size: 16px; line-height: 24px; color: var(--ink); font-style: normal;
  }
  .brand {
    position: absolute; left: 370px; right: 0; top: 80px;
    text-align: center;
  }
  .brand__dot {
    width: 76px; height: 76px; border-radius: 50%;
    margin: 0 auto 18px;
    background: linear-gradient(135deg, var(--violet), var(--pink));
  }
  .brand__name {
    font-weight: 900; font-size: 32px; line-height: 36px;
    color: var(--white); text-transform: uppercase; letter-spacing: 1px;
  }
  .brand__tag {
    margin-top: 8px; font-size: 8.5px; font-weight: 500;
    letter-spacing: 1px; color: var(--pink); text-transform: uppercase;
  }
</style>
</head>
<body>
  <section class="card card--front" aria-label="Card front">
    <div class="front__brand">Stride &amp; Tempo</div>
    <div class="front__services">PERSONAL TRAINING &nbsp;|&nbsp; NUTRITION &nbsp;|&nbsp; MOTIVATION</div>
  </section>

  <section class="card card--back" aria-label="Card back">
    <svg class="back__panel" viewBox="0 0 618 374" preserveAspectRatio="none" aria-hidden="true">
      <defs>
        <linearGradient id="edge" x1="0" y1="0" x2="0" y2="1">
          <stop offset="0" stop-color="#5a3a8c"/>
          <stop offset="1" stop-color="#b062b0"/>
        </linearGradient>
      </defs>
      <path d="M384 0 C330 80 300 200 388 374 L618 374 L618 0 Z" fill="url(#edge)"/>
      <path d="M384 0 C338 80 318 200 404 374 L618 374 L618 0 Z" fill="#050505"/>
    </svg>

    <div class="person__name">MARK STRIDE</div>
    <div class="person__role">Personal Trainer</div>
    <ul class="contact">
      <li><svg viewBox="0 0 24 24"><path d="M6.6 10.8a15 15 0 0 0 6.6 6.6l2.2-2.2c.3-.3.7-.4 1-.2 1.1.4 2.3.6 3.6.6.6 0 1 .4 1 1V20c0 .6-.4 1-1 1A17 17 0 0 1 3 4c0-.6.4-1 1-1h3.5c.6 0 1 .4 1 1 0 1.3.2 2.5.6 3.6.1.3 0 .7-.2 1z"/></svg>+1 (555) 014-2290</li>
      <li><svg viewBox="0 0 24 24"><path d="M2 5h20v14H2z M2 5l10 8 10-8" stroke="#efefef" stroke-width="1.5"/></svg>mark@strideandtempo.com</li>
      <li><svg viewBox="0 0 24 24"><circle cx="12" cy="12" r="9"/><path d="M3 12h18M12 3c3 3 3 15 0 18M12 3c-3 3-3 15 0 18" stroke="#efefef" stroke-width="1.3" fill="none"/></svg>www.strideandtempo.com</li>
    </ul>
    <address class="address">1820 Maple Ridge Drive<br>Fairview Texas 75069</address>

    <div class="brand">
      <div class="brand__dot"></div>
      <div class="brand__name">Stride<br>&amp; Tempo</div>
      <div class="brand__tag">Personal training. Nutrition. Motivation</div>
    </div>
  </section>
</body>
</html>
```